The Quiet Harvest Book Cover

Cover for Multiauthor Ebook & Paper Print Book Cover

Book Title:
The Quiet Harvest: Lessons of Insight From A Circle of Mentors to Guide You Toward a Fuller Journey

This book will offer the wisdom and philosophies of a variety of different coaches to allow future clients to get a taste of you and your style and prepare them to work with you!

A coach does not fix you. Or heal you. They coach you - offer thoughts to ponder, guidance, techniques to try. All to help you plays and succeed at the game of life.

Each coach has their own personality, training, experience, method and philosophy they bring to the table. The underlying purpose is to guide you through the quiet harvest, to become the person you desire and aspire to be. Different coaches for different folks, yet they all have their own unique wisdom and special sauce to share.

This book is a collection of just that. A tasting of the wisdom and philosophies of a variety of different coaches for you to experience.

Types of Coaches: Clarity, Dreams, Goals, Motivation, Mindset,  Subconscious, Beliefs, Behavior, Accountability, Life, Wellness, Love & Dating, Relationships, Sex, Business, Career,  Executive,  Personal Development,  Writing, Wellness, Fitness, Parenting,  Style, Spirituality, Public Speaking, Financial,  Time management, Weight Loss, Running, Self esteem,  Tarot, Astrology, Enneagram, Soul path/ Dharma, Skills, Performance,  Speaking / Communication, Leadership, Shadow Work, Acting, Sports, ANY & ALL

Target Market(s)

Males or females looking for guidance and words of wisdom from an expert coach - maybe to find one that resonates with them to work with further. Ages 16 and up. Any Gender. International. Looking to improve their life!

Industry/Entity Type

Self Development, Wellness, Coaching, Personal Growth, Fitness, Spirituality, Business, Relationships

Font styles to use
Serif
Script

Colors
0054AA
0677BA
7BADD7
CADEEF
E8F1F8
FFF300
FFF600
FEFA6F
FFFEC7
FFFEE8

Requirements
Must have
• I am looking for a visually appealing, unique cover that encompasses the breadth and depth of the transformation that people can go through and inspires them to want to grow and change even more. I love when elegant and classic simplicity is combined with some kind of twist that catches the eye and provokes thought. I love complimentary fonts, colors, design elements. You can visit my Brindlemart Author Page - Dr. Marisol Pendergast Voyle to see my titles to see what I have liked! But I am also excited to see where you can make my vision even better!!
Nice to have
• Front Cover - Image, Title and Subtitle, The Lantern Publishing House, Spine - Title and Publishing House Logo, Back - Book Blurb, Authors Names, Info about Publishing House, ISBN Barcode
Should not have
• Anything too feminine or too masculine as I want to encourage coaches of all genders to participate.

```html
<!DOCTYPE html>
<html lang="en">
<head>
<meta charset="utf-8">
<title>The Quiet Harvest — Book Cover Wrap</title>
<link rel="stylesheet" href="https://fonts.googleapis.com/css2?family=Allura&family=Marcellus&family=Old+Standard+TT:wght@400;700&family=Open+Sans:wght@400;600&family=Lato:wght@400&display=swap">
<style>
  :root {
    --stage: #e6e9f2;
    --cover-grey: #b9b9b9;
    --cover-grey-light: #c8c8c8;
    --navy: #1b2350;
    --band-navy: #27315c;
    --ink-white: #f4f4f6;
    --script-white: #ffffff;
    --body-white: #f7f7f9;
    --wing-dark: #0d1630;
    --wing-blue: #1f6fb8;
    --wing-cyan: #5fc0e8;
    --band-height: 175px;
  }
  * { box-sizing: border-box; margin: 0; padding: 0; }
  html, body { width: 1200px; height: 849px; overflow: hidden; }
  body { background: var(--stage); position: relative; }

  .wrap {
    position: absolute; left: 95px; top: 64px;
    width: 1010px; height: 720px; display: flex;
    box-shadow: 0 10px 30px rgba(20, 30, 70, .25);
  }

  /* Back cover */
  .back { position: relative; width: 480px; height: 720px; overflow: hidden;
    background: linear-gradient(90deg, var(--cover-grey), var(--cover-grey-light)); }
  .back-title { position: absolute; left: 40px; top: 40px; right: 40px;
    font-family: "Old Standard TT", serif; color: var(--navy); }
  .back-title h2 { font-size: 30px; font-weight: 700; letter-spacing: .5px; transform: scaleX(.82); transform-origin: left; white-space: nowrap; }
  .back-title p { font-size: 10.5px; text-transform: uppercase; letter-spacing: .5px; line-height: 1.25; margin-top: 4px; }
  .blurb { position: absolute; left: 40px; right: 40px; top: 122px;
    font-family: "Open Sans", sans-serif; font-size: 10.5px; line-height: 1.55; color: var(--body-white); text-align: justify; }
  .blurb p + p { margin-top: 10px; }
  .authors-head { position: absolute; left: 0; right: 0; top: 352px; text-align: center;
    font-family: "Open Sans", sans-serif; font-size: 11px; color: var(--navy); }
  .authors { position: absolute; left: 90px; right: 90px; top: 374px; display: flex; justify-content: space-between;
    font-family: "Open Sans", sans-serif; font-size: 10.5px; color: var(--navy); line-height: 16.5px; }
  .authors ul { list-style: none; }
  .publisher-band { position: absolute; left: 0; right: 0; bottom: 0; height: var(--band-height); background: var(--band-navy);
    padding: 14px 40px; color: var(--ink-white); font-family: "Open Sans", sans-serif; }
  .publisher-band h3 { font-weight: 400; font-size: 11.5px; text-align: center; margin-bottom: 6px; }
  .publisher-band p { font-size: 10.5px; line-height: 1.55; text-align: justify; }

  /* Spine */
  .spine { position: relative; width: 50px; height: 720px; overflow: hidden;
    background: linear-gradient(90deg, #c4c4c4, #b4b4b4); }
  .spine-band { position: absolute; left: 0; right: 0; bottom: 0; height: var(--band-height); background: var(--band-navy); }
  .spine-title { position: absolute; left: 25px; top: 40px; transform-origin: left top; transform: rotate(90deg) translateY(-50%);
    white-space: nowrap; display: flex; align-items: baseline; gap: 6px; }
  .spine-title .script { font-family: "Allura", cursive; font-size: 40px; color: var(--script-white); }
  .spine-title .serif { font-family: "Marcellus", serif; font-size: 22px; color: var(--navy); letter-spacing: 1px; }
  .spine-mark { position: absolute; left: 18px; top: 560px; width: 14px; height: 14px; border-radius: 50%; background: var(--ink-white); }
  .spine-publisher { position: absolute; left: 25px; top: 582px; transform-origin: left top; transform: rotate(90deg) translateY(-50%);
    white-space: nowrap; font-family: "Lato", sans-serif; font-size: 7.5px; line-height: 1; color: var(--ink-white); text-transform: uppercase; }

  /* Front cover */
  .front { position: relative; width: 480px; height: 720px;
    background: linear-gradient(180deg, #bdbdbd, #b2b2b2); overflow: hidden; }
  .swoosh { position: absolute; left: 0; top: 0; }
  .title-the { position: absolute; left: 50px; top: 10px; font-family: "Allura", cursive; font-size: 130px; color: var(--script-white); line-height: 1; }
  .title-main { position: absolute; left: 150px; top: 120px; font-family: "Marcellus", serif; font-size: 64px; color: var(--navy); letter-spacing: 2px;
    text-shadow: 1px 1px 0 rgba(255,255,255,.6); }
  .title-end { position: absolute; left: 110px; top: 160px; font-family: "Allura", cursive; font-size: 120px; color: var(--script-white); line-height: 1; }
  .cover-art { position: absolute; left: 100px; top: 340px; width: 280px; height: 200px; }
  .subtitle { position: absolute; left: 40px; right: 40px; top: 580px; text-align: center;
    font-family: "Old Standard TT", serif; font-size: 15px; line-height: 1.2; color: var(--ink-white); text-transform: uppercase; letter-spacing: .5px; }
  .imprint { position: absolute; left: 0; right: 0; top: 650px; text-align: center; }
  .imprint-mark { display: block; margin: 0 auto 6px; width: 22px; height: 22px; border-radius: 50%; background: var(--navy); }
  .imprint-name { font-family: "Lato", sans-serif; font-size: 14px; color: var(--navy); }
</style>
</head>
<body>
  <main class="wrap">
    <section class="back">
      <header class="back-title">
        <h2>THE QUIET HARVEST</h2>
        <p>Lessons of insight from a circle of mentors<br>to guide you toward a fuller journey</p>
      </header>
      <div class="blurb">
        <p>A coach does not fix you. Or heal you. They coach you - by offering thoughts to ponder, guidance, techniques to try - All to help you play and succeed at the game of life.</p>
        <p>Each coach has their own personality, training, experience, method and philosophy they bring to the table. The underlying purpose is to guide you through the quiet harvest, to become the person you desire and aspire to be. Different coaches for different folks, yet they all have their own unique wisdom and special sauce to share.</p>
        <p>This book is a collection of just that. A tasting of the wisdom and philosophies of a variety of different coaches for you to experience.</p>
      </div>
      <div class="authors-head">Authors names</div>
      <div class="authors">
        <ul><li>Author name</li><li>Author name</li><li>Author name</li><li>Author name</li><li>Author name</li><li>Author name</li><li>Author name</li><li>Author name</li><li>Author name</li><li>Author name</li></ul>
        <ul><li>Author name</li><li>Author name</li><li>Author name</li><li>Author name</li><li>Author name</li><li>Author name</li><li>Author name</li><li>Author name</li><li>Author name</li><li>Author name</li></ul>
      </div>
      <footer class="publisher-band">
        <h3>About the Publisher</h3>
        <p>The Lantern Publishing House is the publishing arm of Lantern Path Wellness, a company founded and led by Dr. Marisol Voyle DPT in order to educate, inspire, and empower healing and love for oneself and for others. The Lantern Publishing House seeks to unlock the potential of each individual to amplify their voice and message to improve our human experience. Please visit lanternpathwellness.net to learn about future publications.</p>
      </footer>
    </section>

    <section class="spine">
      <div class="spine-band"></div>
      <div class="spine-title"><span class="script">the</span><span class="serif">QUIET</span><span class="script">harvest</span></div>
      <span class="spine-mark"></span>
      <div class="spine-publisher">The Lantern Publishing House</div>
    </section>

    <section class="front">
      <svg class="swoosh" width="480" height="720" viewBox="0 0 480 720" aria-hidden="true">
        <path d="M0 125 C 60 120, 110 110, 150 80" fill="none" stroke="#ffffff" stroke-width="1.2"/>
        <path d="M300 250 C 360 235, 420 200, 480 190" fill="none" stroke="#ffffff" stroke-width="1.2"/>
      </svg>
      <div class="title-the">the</div>
      <div class="title-main">QUIET</div>
      <div class="title-end">harvest</div>
      <svg class="cover-art" viewBox="0 0 280 200" role="img" aria-label="Illustration of a dark blue butterfly with bright cyan wing markings">
        <defs>
          <radialGradient id="artTone" cx="50%" cy="65%" r="60%">
            <stop offset="0%" stop-color="#5fc0e8"/>
            <stop offset="45%" stop-color="#1f6fb8"/>
            <stop offset="100%" stop-color="#0d1630"/>
          </radialGradient>
        </defs>
        <rect width="280" height="200" rx="18" fill="url(#artTone)"/>
      </svg>
      <p class="subtitle">Lessons of insight from a circle<br>of mentors to guide you toward<br>a fuller journey</p>
      <div class="imprint">
        <span class="imprint-mark"></span>
        <span class="imprint-name">The Lantern Publishing House</span>
      </div>
    </section>
  </main>
</body>
</html>
```